New Business Card Design Project

Use the flyer uploaded and website www.brightoakbuilders.com for inspiration.
List Our Services on Backside of business cards
Marcus Delling
Harborline Builders Inc.
Licensed General Contractors
858-471-6093

Contact Information for Business Card

Use the flyer uploaded and website www.brightoakbuilders.com for inspiration. List Our Services on Backside of business cards Marcus Delling Harborline Builders Inc. Licensed General Contractors 858-471-6093

```html
<!DOCTYPE html>
<html lang="en">
<head>
<meta charset="utf-8">
<title>Harborline Builders – Business Card</title>
<link href="https://fonts.googleapis.com/css2?family=Lato:wght@400;700;900&display=swap" rel="stylesheet">
<style>
  :root{
    --backdrop:#2a2a2c;
    --card-blue:#3a84c9;
    --card-white:#ffffff;
    --ink:#1c1c1c;
    --ink-soft:#333333;
    --accent-blue:#2f7fd0;
    --accent-red:#e2323c;
    --label-ink:#1a1a1a;
  }
  *{margin:0;padding:0;box-sizing:border-box}
  html,body{width:1200px;height:900px;overflow:hidden;background:var(--backdrop)}
  .stage{position:relative;width:1200px;height:900px}
  .card{position:absolute;left:250px;width:700px;height:400px;overflow:hidden;box-shadow:0 10px 30px rgba(0,0,0,.45)}
  .card--back{top:28px;background:var(--card-blue)}
  .card--front{top:472px;background:var(--card-white)}

  /* back side */
  .service{position:absolute;height:118px;display:flex;align-items:flex-end;justify-content:center;padding-bottom:10px}
  .service__label{font-family:"Lato",sans-serif;font-weight:700;font-size:12px;letter-spacing:.5px;color:var(--label-ink);text-transform:uppercase;background:rgba(255,255,255,.55);padding:2px 6px}
  .service--painting{top:18px;left:40px;width:200px;background:linear-gradient(135deg,#2c2c2c,#c86a2a 45%,#d9c7a4 70%,#4a7fb8)}
  .service--flooring{top:18px;left:250px;width:200px;background:linear-gradient(135deg,#8e8270,#c9bba3 50%,#6f6f72)}
  .service--kitchens{top:18px;left:460px;width:210px;background:linear-gradient(135deg,#e8d7b6,#f4efe6 55%,#d8d8d8)}
  .service--bathrooms{top:262px;left:30px;width:200px;background:linear-gradient(135deg,#f0f0ee,#d9dede 55%,#c8ccc9)}
  .service--energy{top:262px;left:240px;width:210px;background:linear-gradient(135deg,#9da2a4,#e3e3e1 55%,#b9aa92)}
  .service--custom{top:262px;left:460px;width:210px;background:linear-gradient(135deg,#c98a4c,#e9c597 55%,#f1ebe2)}

  .back-title{position:absolute;top:172px;left:0;width:700px;text-align:center;font-family:"Lato",sans-serif;font-weight:700;font-size:44px;letter-spacing:2px;line-height:1;color:var(--card-white);text-transform:uppercase}

  /* front side */
  .brand{position:absolute;top:110px;left:56px;font-family:"Lato",sans-serif;font-weight:700;font-size:30px;letter-spacing:1px;line-height:1;color:var(--ink);text-transform:uppercase}

  .contact{position:absolute;top:196px;left:56px;list-style:none;font-family:"Lato",sans-serif;color:var(--ink-soft)}
  .contact__item{display:flex;align-items:center;gap:10px;font-size:17px;line-height:30px}
  .contact__item svg{width:16px;height:16px;flex:none;fill:var(--accent-blue)}
  .contact__phone{font-weight:900;font-size:19px;color:var(--ink)}

  .person{position:absolute;left:370px;top:318px;font-family:"Lato",sans-serif}
  .person__name{font-weight:900;font-size:34px;letter-spacing:1px;color:var(--accent-blue);text-transform:uppercase;line-height:1}
  .person__role{font-size:19px;color:var(--accent-red);margin-top:4px}
</style>
</head>
<body>
<main class="stage">

  <section class="card card--back" aria-label="Business card back – services">
    <div class="service service--painting" role="img" aria-label="Photo of open paint cans with a colour fan"><span class="service__label">Painting</span></div>
    <div class="service service--flooring" role="img" aria-label="Photo of carpet and flooring samples"><span class="service__label">Flooring</span></div>
    <div class="service service--kitchens" role="img" aria-label="Photo of a bright kitchen blending into a sketch"><span class="service__label">Kitchens</span></div>

    <div class="back-title">Harborline Builders</div>

    <div class="service service--bathrooms" role="img" aria-label="Photo of a white bathroom with glass shower"><span class="service__label">Bathrooms</span></div>
    <div class="service service--energy" role="img" aria-label="Photo of a modern lit living space"><span class="service__label">Energy Efficient Upgrades</span></div>
    <div class="service service--custom" role="img" aria-label="Photo of house framing blending into a finished kitchen"><span class="service__label">Custom Renovations</span></div>
  </section>

  <section class="card card--front" aria-label="Business card front – contact">
    <div class="brand">Harborline Builders</div>

    <ul class="contact">
      <li class="contact__item">
        <svg viewBox="0 0 24 24"><path d="M6.6 10.8a15.1 15.1 0 0 0 6.6 6.6l2.2-2.2c.3-.3.7-.4 1-.2 1.1.4 2.3.6 3.6.6.6 0 1 .4 1 1V20c0 .6-.4 1-1 1A17 17 0 0 1 3 4c0-.6.4-1 1-1h3.5c.6 0 1 .4 1 1 0 1.3.2 2.5.6 3.6.1.3 0 .7-.2 1z"/></svg>
        <span><span class="contact__phone">858-471-6093</span> Call/Text</span>
      </li>
      <li class="contact__item">
        <svg viewBox="0 0 24 24"><path d="M2 5h20v14H2zm2 2v.5l8 5 8-5V7l-8 5z"/></svg>
        <span>info@brightoakbuilders.com</span>
      </li>
      <li class="contact__item">
        <svg viewBox="0 0 24 24"><path d="M12 2a10 10 0 1 0 0 20 10 10 0 0 0 0-20zm0 2c1 0 2.3 2 2.8 5H9.2C9.7 6 11 4 12 4zM4.3 11h3.8c0 1 .1 1.8.2 2.6H4.6A8 8 0 0 1 4.3 11zm5.8 0h3.8c0 1-.1 1.8-.2 2.6h-3.4c-.1-.8-.2-1.6-.2-2.6zm5.8 0h3.8a8 8 0 0 1-.3 2.6h-3.7c.1-.8.2-1.6.2-2.6z"/></svg>
        <span>brightoakbuilders.com</span>
      </li>
      <li class="contact__item">
        <svg viewBox="0 0 24 24"><path d="M12 2a7 7 0 0 0-7 7c0 5 7 13 7 13s7-8 7-13a7 7 0 0 0-7-7zm0 9.5A2.5 2.5 0 1 1 12 6.5a2.5 2.5 0 0 1 0 5z"/></svg>
        <span>Harborline Builders Inc.</span>
      </li>
    </ul>

    <div class="person">
      <div class="person__name">Marcus Delling</div>
      <div class="person__role">Licensed General Contractors</div>
    </div>
  </section>

</main>
</body>
</html>
```